Verodex business card

Business card for sustainable investment company called "Verodex". Verodex is an exchange platform selling carbon credits between buyers and sellers. Carbon Credits are an environmental commodity for reducing global carbon emissions.

the card should obviously have our logo and the theme should be sustainability/environment mixed with a trading platform.

Contact Information for Business Card

Logo, Name, Title, Phone, Email

Colors
0054AA
0677BA
7BADD7
CADEEF
E8F1F8
0094D4
00A9DD
6FCCEA
C7EBF8
E9F6FB
00AB8E
00BBA5
67D7C9
C6EFE9
E9F9F6
59FF00
82FF00
B8FF75
E3FFCB
F4FFEA

```html
<!DOCTYPE html>
<html lang="en">
<head>
<meta charset="utf-8">
<title>Verodex Business Card</title>
<link href="https://fonts.googleapis.com/css2?family=Lexend:wght@300;400;500;600&display=swap" rel="stylesheet">
<style>
  :root {
    --backdrop: #e2e2e2;
    --front-light: #f6f6f6;
    --front-shade: #e9e9ea;
    --navy-deep: #14233b;
    --navy: #1c2d4a;
    --ink: #1f3350;
    --teal: #4fb3c8;
    --blue: #3a6fc0;
    --accent-line: #3d7fc6;
    --icon: #5aa7d8;
    --text-light: #e6ebf2;
  }
  * { margin: 0; padding: 0; box-sizing: border-box; }
  html, body {
    width: 1200px; height: 1200px; overflow: hidden;
    background: var(--backdrop);
    font-family: "Lexend", sans-serif;
  }
  .canvas { position: relative; width: 1200px; height: 1200px; }
  .card {
    position: absolute; left: 235px; width: 730px; height: 417px;
    overflow: hidden;
  }
  .card-front {
    top: 160px;
    background: linear-gradient(100deg, var(--front-shade) 0%, var(--front-light) 55%, #fbfbfb 100%);
  }
  .card-back {
    top: 632px;
    background: linear-gradient(110deg, var(--navy-deep) 0%, var(--navy) 60%, #213556 100%);
  }
  .brand-name {
    position: absolute; left: 0; right: 0; top: 172px;
    text-align: center;
    font-weight: 600; font-size: 58px; letter-spacing: 1px;
    color: var(--ink); line-height: 1;
  }
  .person {
    position: absolute; right: 450px; top: 180px; text-align: right;
    white-space: nowrap;
  }
  .person-name {
    font-weight: 600; font-size: 33px; line-height: 1.1;
    background: linear-gradient(90deg, var(--teal), var(--blue));
    -webkit-background-clip: text; background-clip: text; color: transparent;
  }
  .person-title {
    font-weight: 300; font-size: 19px; color: var(--text-light);
    margin-top: 6px;
  }
  .divider {
    position: absolute; left: 315px; top: 141px; width: 2px; height: 132px;
    background: var(--accent-line);
  }
  .contact {
    position: absolute; left: 355px; top: 140px;
    color: var(--text-light); font-size: 18.5px; font-weight: 300;
    white-space: nowrap;
  }
  .office-name { font-weight: 500; line-height: 26px; }
  .office-address { line-height: 26px; margin-bottom: 10px; }
  .contact-row { display: flex; align-items: center; gap: 8px; line-height: 28px; }
  .contact-row svg { width: 15px; height: 15px; flex: none; }
</style>
</head>
<body>
<div class="canvas">
  <section class="card card-front">
    <div class="brand-name">VERODEX</div>
  </section>

  <section class="card card-back">
    <div class="person">
      <div class="person-name">Marek Halvorsen</div>
      <div class="person-title">Sales Representative</div>
    </div>
    <div class="divider"></div>
    <div class="contact">
      <div class="office-name">Verodex Head Office</div>
      <div class="office-address">Budapest XIII. Lomber utca 14.</div>
      <div class="contact-row">
        <svg viewBox="0 0 16 16" aria-hidden="true"><path fill="var(--icon)" d="M3.2 1.5l2.3 2.6-1.1 1.7c.8 1.9 2.2 3.4 4.1 4.3l1.7-1.1 2.6 2.3-1.3 2.2C6.6 13.3 2.4 9 1.1 3.9z"/><path fill="none" stroke="var(--icon)" stroke-width="1.2" d="M9.5 3.5a3.5 3.5 0 0 1 3 3M9.5 1a6 6 0 0 1 5.5 5.5"/></svg>
        <span>+36 30 412 5590</span>
      </div>
      <div class="contact-row">
        <svg viewBox="0 0 16 16" aria-hidden="true"><rect x="1" y="3" width="14" height="10" fill="var(--icon)"/><path d="M1.5 3.5L8 9l6.5-5.5" fill="none" stroke="var(--navy)" stroke-width="1.3"/></svg>
        <span>szerviz@verodex.com</span>
      </div>
      <div class="contact-row">
        <svg viewBox="0 0 16 16" aria-hidden="true"><circle cx="8" cy="8" r="7" fill="var(--icon)"/><path d="M1 8h14M8 1c-3 3.5-3 10.5 0 14M8 1c3 3.5 3 10.5 0 14" fill="none" stroke="var(--navy)" stroke-width="1.1"/></svg>
        <span>www.verodex.com</span>
      </div>
    </div>
  </section>
</div>
</body>
</html>
```